Business Card Design

We provide services doing multiple jobs in the construction industry.Please note: The company name needs to be ROCK SOLID BUILDING SERVICESAttached logo was an example of what we wanted. Can you change up the colors?

Industry/Entity Type

Construction

Contact Information for Business Card

ROCK SOLID BUILDING SERVICES5401 HUDSON BEND RDAUSTIN, TX 78734(512)243-6854ROCKSOLIDBUILDINGSERVICES@GMAIL.COM

```html
<!DOCTYPE html>
<html lang="en">
<head>
<meta charset="utf-8">
<title>Pearlwood Framing Works — Business Card</title>
<link rel="stylesheet" href="https://fonts.googleapis.com/css2?family=Oswald:wght@600&family=Roboto:wght@300;400&display=swap">
<style>
  :root {
    --backdrop: #e6e6e4;
    --card-black: #050505;
    --card-white: #ffffff;
    --steel-blue: #5f7f98;
    --stone-grey: #a9a9a9;
    --ink-white: #f2f2f2;
    --card-shadow: rgba(0, 0, 0, 0.25);
  }
  * { margin: 0; padding: 0; box-sizing: border-box; }
  html, body {
    width: 1200px;
    height: 817px;
    overflow: hidden;
    background: var(--backdrop);
  }
  .canvas {
    position: relative;
    width: 1200px;
    height: 817px;
    display: flex;
    align-items: center;
    justify-content: center;
    gap: 60px;
  }
  .card {
    position: relative;
    width: 520px;
    height: 297px;
    border-radius: 4px;
    overflow: hidden;
    box-shadow: 0 10px 28px var(--card-shadow);
  }

  /* Front side */
  .card-front {
    background: var(--card-black);
    color: var(--ink-white);
  }
  .brand {
    position: absolute;
    top: 48px;
    left: 0;
    right: 0;
    display: flex;
    align-items: center;
    justify-content: center;
    gap: 18px;
  }
  .brand-mark {
    width: 64px;
    height: 64px;
    background: var(--stone-grey);
  }
  .brand-name {
    font-family: "Oswald", sans-serif;
    font-weight: 600;
    color: var(--steel-blue);
    line-height: 1;
    text-transform: uppercase;
  }
  .brand-name .primary { display: block; font-size: 48px; letter-spacing: 1px; }
  .brand-name .secondary { display: block; font-size: 17px; letter-spacing: 3px; margin-top: 4px; }
  .contact {
    position: absolute;
    left: 0;
    right: 0;
    bottom: 46px;
    text-align: center;
    font-family: "Roboto", sans-serif;
    font-weight: 300;
    font-size: 13px;
    letter-spacing: 0.4px;
    line-height: 1.85;
    text-transform: uppercase;
  }
  .contact .phone { font-size: 12px; }

  /* Back side */
  .card-back { background: var(--card-black); }
  .card-back .swoosh {
    position: absolute;
    inset: 0;
    width: 100%;
    height: 100%;
  }
  .back-name {
    position: absolute;
    top: 50%;
    left: 58px;
    transform: translateY(-50%);
    display: flex;
    align-items: center;
    gap: 12px;
    font-family: "Oswald", sans-serif;
    font-weight: 600;
    font-size: 30px;
    line-height: 1.05;
    color: var(--steel-blue);
    text-transform: uppercase;
  }
  .back-name .dot {
    width: 22px;
    height: 22px;
    border-radius: 50%;
    background: var(--steel-blue);
    flex: none;
  }
</style>
</head>
<body>
  <main class="canvas">
    <section class="card card-front" aria-label="Business card front">
      <div class="brand">
        <span class="brand-mark" aria-hidden="true"></span>
        <h1 class="brand-name">
          <span class="primary">Pearlwood</span>
          <span class="secondary">Framing Works</span>
        </h1>
      </div>
      <address class="contact" style="font-style: normal;">
        <div class="phone">(512)555-0193</div>
        <div>7732 Fernglen Pass Ln Austin, TX 78734</div>
        <div>pearlwoodframingworks@mailnest.example</div>
      </address>
    </section>

    <section class="card card-back" aria-label="Business card back">
      <svg class="swoosh" viewBox="0 0 520 297" preserveAspectRatio="none" aria-hidden="true">
        <path d="M0 0 H330 C400 60 420 190 380 297 H0 Z" fill="var(--card-white)"/>
        <path d="M330 0 C400 60 420 190 380 297 L392 297 C436 190 414 56 344 0 Z" fill="var(--steel-blue)"/>
        <path d="M360 0 C430 70 448 190 412 297 L416 297 C454 190 436 66 366 0 Z" fill="var(--steel-blue)"/>
      </svg>
      <div class="back-name">
        <span class="dot" aria-hidden="true"></span>
        <span>Pearlwood<br>Plumbing Co</span>
      </div>
    </section>
  </main>
</body>
</html>
```